Web Design Project

We are an IT System Integrator. We provide Korvin 450 ERP System, CRM etc. We also provide hardware, networking servicing. Please look at www.zolvantix.com.sg. They provide the same service as us. We like to redesign our web site. I will attached the color that I prefer for reference.

Our website is www.tadurk.com.sg.  It has been created about 14 years ago.  We are trying to revamp it with a new look and information.   The new website must be informative, fast.    I have attached an attachment which show the color that I prefer(brownish golden).   

Our competitor (www.zolvantix.com) is carrying the same trade as us.  They have all the informations In their website that we will like to have.  Therefore I recommend you to take a look at my competitor website and have a better   
understanding on the kind of information I would like to have for my new website.

This project is guarantee to the person with the best design.  We can have it guarantee.

Target Market(s)

Corporate and companies

Industry/Entity Type

Hardware

```html
<!DOCTYPE html>
<html lang="en">
<head>
<meta charset="utf-8">
<title>Veltrano Information System</title>
<link rel="stylesheet" href="https://fonts.googleapis.com/css2?family=Ubuntu:ital,wght@0,300;0,400;0,500;1,300&display=swap">
<style>
:root{
  --gold-dark:#8b6a35;
  --gold-band:#a9884f;
  --gold-top:#a48248;
  --gold-fade:#c9ad7b;
  --gold-accent:#8a6a2c;
  --gold-title:#9b7430;
  --testi-top:#d1a745;
  --testi-bottom:#bd8a17;
  --ink:#3e3424;
  --body:#6b5a40;
  --muted:#777;
  --line:#e2e2e2;
  --footer:#f3f3f3;
}
*{margin:0;padding:0;box-sizing:border-box}
html,body{width:1059px;height:1200px;overflow:hidden;background:#fff;font-family:"Ubuntu",sans-serif}
.page{position:relative;width:1059px;height:1200px;
  background:linear-gradient(to bottom,var(--gold-top) 110px,var(--gold-fade) 330px,#d6be92 402px,#fff 402px)}
.util-bar{position:absolute;left:0;top:0;width:100%;height:40px;background:var(--gold-dark)}
.nav-band{position:absolute;left:0;top:40px;width:100%;height:70px;background:var(--gold-band)}
.util-links{position:absolute;right:94px;top:10px;font-size:12px;color:#f5ead6;font-weight:300;display:flex;gap:11px}
.util-links span.sep{opacity:.8}
.brand{position:absolute;left:62px;top:16px;width:178px;height:110px;border-radius:20px;
  background:linear-gradient(#c5a46c,#b49055);display:flex;flex-direction:column;align-items:center;justify-content:center;gap:6px}
.brand-name{font-size:26px;font-weight:500;color:#f6ead2;letter-spacing:.5px}
.brand-sub{font-size:10px;font-weight:400;color:#f6ead2}
.main-nav{position:absolute;left:420px;top:58px;display:flex;align-items:center;height:34px;font-size:15px;color:#fff}
.main-nav a{color:#fff;text-decoration:none;padding:0 13px;line-height:34px}
.main-nav a.active{background:#6f5530;border-radius:3px;padding:0 19px;margin-right:2px}
.main-nav .sep{width:1px;height:17px;background:rgba(255,255,255,.45)}
.slider{position:absolute;left:77px;top:143px;width:905px;height:352px}
.slider svg{display:block}
.dots{position:absolute;left:423px;top:320px;display:flex;gap:4px}
.dots i{width:12px;height:12px;border-radius:50%;background:#f2f2f2;display:block}
.welcome{position:absolute;left:81px;top:528px;width:622px}
.welcome h1{font-size:24px;font-weight:400;color:var(--ink);margin-bottom:8px}
.welcome p{font-size:12px;font-weight:300;color:var(--body);line-height:21.2px;margin-bottom:9px}
.welcome p.gap{margin-bottom:30px}
.news{position:absolute;left:729px;top:518px;width:253px;height:296px;border:1px solid var(--line);border-radius:3px;
  background:linear-gradient(#fff,#f3f3f3);padding:16px 21px}
.news h2{font-size:19px;font-weight:400;color:var(--ink);margin-bottom:14px}
.news-item{margin-bottom:16px}
.news-item time{display:block;font-size:12px;color:#3a3a3a;margin-bottom:5px}
.news-item p{font-size:11px;font-weight:300;color:#666;line-height:17.6px}
.testimonial{position:absolute;left:730px;top:830px;width:251px;height:195px;border-radius:3px;
  background:linear-gradient(var(--testi-top),var(--testi-bottom));padding:16px 23px;color:#fff}
.testimonial h2{font-size:20px;font-weight:400;margin-bottom:9px}
.testimonial blockquote{font-size:12px;font-style:italic;font-weight:300;line-height:21.2px;color:#fbeecb;margin-bottom:6px}
.testimonial .author{font-size:12.5px;font-weight:400}
.testimonial .role{font-size:11px;font-weight:300;margin-top:3px}
.feature{position:absolute;top:832px;width:192px}
.feature .thumb{display:block;width:192px;height:95px;border-radius:3px}
.feature h3{font-size:16px;font-weight:400;color:var(--gold-title);margin:12px 0 5px 1px}
.feature p{font-size:11px;font-weight:300;color:#777;line-height:17.6px;margin-left:1px}
.feature a{display:block;font-size:12px;color:#3a3a3a;text-decoration:none;margin:6px 0 0 3px}
.footer{position:absolute;left:0;top:1085px;width:100%;height:115px;background:var(--footer)}
.footer-nav{position:absolute;left:86px;top:30px;font-size:13px;color:#444;display:flex;gap:7px}
.copyright{position:absolute;left:86px;top:58px;font-size:11.5px;font-weight:300;color:#999}
.social{position:absolute;left:890px;top:26px;display:flex;gap:4px}
.social i{display:block;width:25px;height:25px;border-radius:3px}
</style>
</head>
<body>
<div class="page">
  <div class="util-bar"></div>
  <div class="nav-band"></div>
  <nav class="util-links"><span>Sitemap</span><span class="sep">|</span><span>Log In</span><span class="sep">|</span><span>Enquiry</span><span class="sep">|</span><span>Support</span></nav>

  <div class="brand">
    <span class="brand-name">Veltrano</span>
    <span class="brand-sub">Veltrano Information System</span>
  </div>

  <nav class="main-nav">
    <a class="active" href="#">Home</a>
    <a href="#">Products</a><span class="sep"></span>
    <a href="#">LEDGRA</a><span class="sep"></span>
    <a href="#">Services</a><span class="sep"></span>
    <a href="#">Clientele</a><span class="sep"></span>
    <a href="#">Career</a><span class="sep"></span>
    <a href="#">Contact</a>
  </nav>

  <div class="slider">
    <svg width="905" height="352" viewBox="0 0 905 352">
      <defs>
        <linearGradient id="heroTone" x1="0" y1="0" x2="1" y2="0">
          <stop offset="0" stop-color="#a8896a"/>
          <stop offset=".35" stop-color="#c9b7a0"/>
          <stop offset=".6" stop-color="#3d4660"/>
          <stop offset=".85" stop-color="#d9d6d2"/>
          <stop offset="1" stop-color="#eeeae4"/>
        </linearGradient>
      </defs>
      <path d="M0 4 Q0 0 4 0 H901 Q905 0 905 4 V340 Q452 320 0 340 Z" fill="#fff"/>
      <path d="M0 340 Q452 320 905 340 V344 Q452 326 0 344 Z" fill="#e9e9e9"/>
      <path d="M8 8 H896 V333 Q452 305 8 333 Z" fill="url(#heroTone)" role="img" aria-label="Photo of smiling business colleagues in a meeting"/>
    </svg>
    <div class="dots"><i></i><i></i><i></i><i></i></div>
  </div>

  <section class="welcome">
    <h1>Welcome to Veltrano Information System</h1>
    <p class="gap">Mauris vel lacus vitae felis vestibulum volutpat. Etiam est nunc, venenatis in, tristique eu, imperdiet ac, nisl. Cum sociis natoque penatibus et magnis dis parturient montes, nascetur ridiculus mus. In iaculis facilisis massa. Etiam eu urna. Sed porta. Suspendisse quam leo, molestie sed, luctus quis, feugiat in, pede. Fusce tellus. Sed metus augue, convallis et</p>
    <p>Nunc tempus felis vitae urna. Vivamus porttitor, g, purus nisi eleifend libero, a tempus libero lectus feugiat felis. Morbi diam mauris, viverra in, gravida eu, mattis in, ante. Morbi eget arcu. Morbi porta, libero id ullamcorper nonummy, nibh ligula pulvinar metus, eget consectetuer augue nisi quis lacus. Ut ac mi quis lacus mollis aliquam. Curabitur iaculis tempus eros. Curabitur vel mi sit amet magna malesuada ultrices.</p>
    <p>Phasellus felis dolor, scelerisque a, tempus eget, lobortis id, libero. Donec scelerisque leo ac risus. Praesent sit amet est. In dictum, dolor eu dictum porttitor, enim felis viverra mi, eget luctus massa purus quis odio.</p>
  </section>

  <aside class="news">
    <h2>Latest News</h2>
    <div class="news-item"><time>20 July 2013</time><p>Nunc tempus felis vitae urna. Vivamus portti-tor g purus nisi eleifend libero</p></div>
    <div class="news-item"><time>18 July 2013</time><p>Praesent sit amet est. In dictum, dolor eu dictum porttitor enim felis viverra mi</p></div>
    <div class="news-item"><time>15 July 2013</time><p>Nunc tempus felis vitae urna. Vivamus portti-tor g purus nisi eleifend libero</p></div>
  </aside>

  <aside class="testimonial">
    <h2>Testimonials</h2>
    <blockquote>Duis sed tellus et tortor vestibulum gravida. Praesent elementum elit at tellus. Curabitur metus ipsum, luctus eu, malesuada ut, tincidunt sed, diam</blockquote>
    <div class="author">By Author Name</div>
    <div class="role">Team Manager</div>
  </aside>

  <article class="feature" style="left:83px">
    <svg class="thumb" viewBox="0 0 192 95" role="img" aria-label="Photo of a technician working at a desk with a computer"><defs><linearGradient id="t1" x1="0" x2="1"><stop offset="0" stop-color="#e6e6e4"/><stop offset="1" stop-color="#c9c4bc"/></linearGradient></defs><rect width="192" height="95" rx="3" fill="url(#t1)"/></svg>
    <h3>Korvin Certified</h3>
    <p>Nunc tempus felis vitae urna. Vivamus porttitor, g, purus nisi eleifend</p>
    <a href="#">LEARN MORE</a>
  </article>
  <article class="feature" style="left:295px">
    <svg class="thumb" viewBox="0 0 192 95" role="img" aria-label="Photo of a technician in a hardware workshop"><defs><linearGradient id="t2" x1="0" x2="0" y1="0" y2="1"><stop offset="0" stop-color="#cfcac2"/><stop offset="1" stop-color="#4a4744"/></linearGradient></defs><rect width="192" height="95" rx="3" fill="url(#t2)"/></svg>
    <h3>Service Beyond</h3>
    <p>Nunc tempus felis vitae urna. Vivamus porttitor, g, purus nisi eleifend</p>
    <a href="#">LEARN MORE</a>
  </article>
  <article class="feature" style="left:507px">
    <svg class="thumb" viewBox="0 0 192 95" role="img" aria-label="Photo of a business team around a meeting table"><defs><linearGradient id="t3" x1="0" x2="1"><stop offset="0" stop-color="#b8a996"/><stop offset=".6" stop-color="#3b3a40"/><stop offset="1" stop-color="#d8d6d2"/></linearGradient></defs><rect width="192" height="95" rx="3" fill="url(#t3)"/></svg>
    <h3>Latest LEDGRA</h3>
    <p>Nunc tempus felis vitae urna. Vivamus porttitor, g, purus nisi eleifend</p>
    <a href="#">LEARN MORE</a>
  </article>

  <footer class="footer">
    <nav class="footer-nav"><span>Home</span>|<span>Products</span>|<span>LEDGRA</span>|<span>Services</span>|<span>Clientele</span>|<span>Career</span>|<span>Contact</span></nav>
    <div class="copyright">© 2013 Company Name.&nbsp; All right reserved.</div>
    <div class="social" aria-label="Social links"><i style="background:#3ba6df"></i><i style="background:#1f72b0"></i><i style="background:#4a69ad"></i></div>
  </footer>
</div>
</body>
</html>
```